Standard Beer Can Image

We are doing a special release beer can for a high end private golf course community and need a beer can image for it. The can will be a visual collaboration between the golf course and our brand and I need help merging the two into a seamless design. The country club ishttps://www.escondidotexas.com and we are bluegatealeworks.com. Attached are their logo, our logos, a previous can design that they used and a couple of our cans for visual concept and the color ways we work off of. We want their identity to be prevalent on the front of the can with ours being secondary on the back of the can. I do like our “weave” on the side of our cans if we can incorporate that. We will need a style and ABV on the front of the can and can provide that a little later as we get into a design.

```html
<!DOCTYPE html>
<html lang="en">
<head>
<meta charset="utf-8">
<title>Premier Lager – Can Labels</title>
<link rel="stylesheet" href="https://fonts.googleapis.com/css2?family=EB+Garamond:wght@400;500&family=Cinzel:wght@400&family=Allura&display=swap">
<style>
  :root {
    --bg: #eeeeee;
    --cocoa: #3f3232;
    --cocoa-text: #4a3e3e;
    --ball-white: #f6f6f6;
    --ball-shade: #e2e2e2;
    --doodle-grey: #ededed;
    --label-white: #ffffff;
    --rule: #b9b9b9;
    --ink: #1d1d1d;
    --cream: #f3f1dc;
    --weave-light: #e6cfa6;
    --weave-mid: #c9a070;
    --weave-dark: #a87c4f;
    --script-grey: #6b6b6b;
  }
  * { box-sizing: border-box; margin: 0; padding: 0; }
  html, body { width: 1200px; height: 901px; overflow: hidden; }
  body {
    background: var(--bg);
    display: flex;
    align-items: center;
    justify-content: center;
    gap: 70px;
    font-family: "EB Garamond", Georgia, serif;
    color: var(--ink);
  }
  .can-label {
    position: relative;
    width: 360px;
    height: 660px;
    overflow: hidden;
    box-shadow: 0 6px 24px rgba(0,0,0,0.12);
  }

  /* Club can */
  .club .shoulder { height: 80px; background: var(--cocoa); }
  .club .ball-field {
    height: 270px;
    background: radial-gradient(ellipse at 50% 40%, var(--ball-white) 0%, var(--ball-shade) 100%);
    display: flex; flex-direction: column; align-items: center; justify-content: center;
    text-align: center;
  }
  .club .mark {
    width: 22px; height: 22px; border-radius: 50%;
    background: var(--cocoa-text); margin-bottom: 18px;
  }
  .club .club-name {
    font-family: "EB Garamond", Georgia, serif;
    font-weight: 400; font-size: 34px; letter-spacing: 5px;
    color: var(--cocoa-text); line-height: 1;
  }
  .club .club-sub {
    font-family: "EB Garamond", Georgia, serif;
    font-size: 17px; letter-spacing: 4px; color: var(--cocoa-text);
    margin-top: 10px;
  }
  .club .tagline {
    font-family: "Allura", cursive;
    font-size: 30px; color: var(--script-grey); margin-top: 6px;
  }
  .club .doodle-field {
    height: 310px;
    background: linear-gradient(180deg, var(--doodle-grey), #f7f7f7);
    display: flex; flex-direction: column; align-items: center; justify-content: center;
  }

  /* Brewery can */
  .brewery { background: linear-gradient(135deg, var(--weave-light) 0%, var(--weave-mid) 55%, var(--weave-dark) 100%); }
  .brewery .weave-top { height: 70px; }
  .brewery .brand-band {
    height: 240px; background: var(--cream);
    display: flex; flex-direction: column; align-items: center; justify-content: center;
    gap: 14px;
  }
  .brewery .mark { width: 26px; height: 26px; background: var(--ink); }
  .brewery .brand-name {
    font-family: "EB Garamond", Georgia, serif;
    font-weight: 500; font-size: 36px; letter-spacing: 4px; color: var(--ink);
    text-transform: uppercase; text-align: center; line-height: 1.1;
  }
  .brewery .weave-field {
    height: 350px;
    display: flex; flex-direction: column; align-items: center; justify-content: center;
  }

  /* Shared style panel */
  .style-panel {
    background: var(--label-white);
    width: 260px;
    padding: 16px 20px 14px;
    text-align: center;
  }
  .club .style-panel { background: transparent; }
  .style-name { font-size: 44px; font-weight: 400; letter-spacing: 1px; line-height: 1.1; padding-bottom: 8px; border-bottom: 1px solid var(--rule); }
  .style-type { font-size: 26px; letter-spacing: 1px; padding: 8px 0; border-bottom: 1px solid var(--rule); }
  .style-abv { font-size: 26px; padding: 8px 0; border-bottom: 1px solid var(--rule); }
  .volume-tag {
    margin-top: 26px;
    background: var(--cocoa); color: #f2eeee;
    font-size: 14px; letter-spacing: 0.5px;
    padding: 4px 14px;
  }
</style>
</head>
<body>

  <section class="can-label club" aria-label="Club front label">
    <div class="shoulder"></div>
    <div class="ball-field" role="img" aria-label="Golf ball dimple texture behind the club name">
      <span class="mark"></span>
      <h1 class="club-name">PALOMAR RIDGE</h1>
      <p class="club-sub">GOLF &amp; LAKE CLUB</p>
      <p class="tagline">Where Fairways Meet Water</p>
    </div>
    <div class="doodle-field" role="img" aria-label="Light grey pattern of golf sketches: flags, tees, trees and carts">
      <div class="style-panel">
        <p class="style-name">PREMIER</p>
        <p class="style-type">LAGER</p>
        <p class="style-abv">4.3% ALC/VOL</p>
      </div>
      <p class="volume-tag">12FL OZ/ 355ML</p>
    </div>
  </section>

  <section class="can-label brewery" aria-label="Brewery back label">
    <div class="weave-top" role="img" aria-label="Woven tan and brown strap pattern"></div>
    <div class="brand-band">
      <span class="mark"></span>
      <h2 class="brand-name">Bluegate<br>Aleworks</h2>
    </div>
    <div class="weave-field" role="img" aria-label="Woven tan and brown strap pattern">
      <div class="style-panel">
        <p class="style-name">PREMIER</p>
        <p class="style-type">LAGER</p>
        <p class="style-abv">4.3% ALC/VOL</p>
      </div>
      <p class="volume-tag">12FL OZ/ 355ML</p>
    </div>
  </section>

</body>
</html>
```